Sales/Landing Page Redesign for Hunting product

I am looking for a redesign for https://ridgelynoutfitters.com/quarter-pad .

We want to add in the information for our new XL quarterpad found: https://ridgelynoutfitters.com/shop/hunting/xl-big-game-quarter-pad/

We also will be adding a spot for this video: https://www.vidstreamhub.com/watch?v=Zk4TnaR8wqe

We like having the 3 options at the bottom, but the goal for this page is to sell the quarter pad.

Target Market(s)

Western Hunters, campers, outdoorsmen

Industry/Entity Type

Hunting

Number of Pages Required

1 page

Font styles to use
Sans Serif

Requirements
Must have
• a clean design that is geared to sell the product.

```html
<!DOCTYPE html>
<html lang="en">
<head>
<meta charset="utf-8">
<title>Ridgelyn Quarter Pads</title>
<link href="https://fonts.googleapis.com/css2?family=Rajdhani:wght@600;700&family=Lato:ital,wght@0,400;0,700;0,900;1,400&display=swap" rel="stylesheet">
<style>
:root{
  --red:#e8202a;
  --red-band:#ec1c24;
  --ink:#1d1d1f;
  --charcoal:#2b2b2d;
  --grey-text:#666;
  --white:#fff;
  --card-line:#dcdcdc;
  --badge-blue:#2b5fa8;
  --badge-orange:#f39a1e;
  --badge-sky:#3c9ad8;
  --badge-navy:#1f3f7a;
}
*{box-sizing:border-box;margin:0;padding:0}
html,body{width:1200px;height:4320px;overflow:hidden}
body{position:relative;font-family:'Lato',sans-serif;color:var(--ink);background:var(--white)}
.section{position:absolute;left:0;width:1200px;overflow:hidden}
.display{font-family:'Rajdhani',sans-serif;font-weight:700;text-transform:uppercase;letter-spacing:1px}
.accent{color:var(--red)}
.btn{position:absolute;display:flex;align-items:center;justify-content:center;gap:7px;font-weight:700;font-size:14px;color:var(--white);text-transform:uppercase;background:var(--red);text-decoration:none}
.btn svg{width:13px;height:13px}
.brand{font-family:'Lato',sans-serif;font-weight:900;letter-spacing:4px;color:var(--white)}
.photo{position:absolute}

/* hero */
.hero{top:0;height:714px;background:linear-gradient(180deg,#3c3a3d 0%,#5a4640 40%,#8a5a44 70%,#6e4a3a 100%)}
.hero .brand{position:absolute;left:144px;top:36px;font-size:30px}
.nav{position:absolute;top:46px;left:0;width:1200px;font-size:14px;color:var(--white)}
.nav span{position:absolute}
.nav .active::after{content:"";position:absolute;left:0;right:0;top:28px;height:2px;background:var(--red)}
.hero h1{position:absolute;top:235px;width:100%;text-align:center;font-size:60px;line-height:68px;color:var(--white)}
.hero .tagline{position:absolute;top:406px;width:100%;text-align:center;font-weight:700;font-size:20px;color:var(--white)}
.hero .tagline i{color:var(--red);font-style:normal;margin:0 4px}
.btn-dark{background:#111}
.play{position:absolute;left:572px;top:584px}

/* problems */
.problems{top:714px;height:617px;background:var(--white)}
.problems h2{position:absolute;left:670px;top:78px;font-size:46px}
.checklist{position:absolute;left:672px;top:165px;list-style:none}
.checklist li{display:flex;align-items:center;gap:20px;height:42.5px;font-size:17px;color:var(--grey-text)}
.better{position:absolute;left:672px;top:405px;font-weight:900;font-size:18px}

/* benefits */
.benefits{top:1331px;height:719px;background:linear-gradient(180deg,#3b3c3d 0%,#2e2f30 50%,#3a3528 100%)}
.benefits h2{position:absolute;top:108px;width:100%;text-align:center;font-size:46px;color:var(--white)}
.feature{position:absolute;top:256px;width:200px;margin-left:-100px;text-align:center;color:var(--white);font-weight:900;font-size:17px;line-height:27px;text-transform:uppercase}
.feature .ring{width:138px;height:138px;margin:0 auto 14px;border:3px solid var(--white);border-radius:50%;background:rgba(255,255,255,.06);display:flex;align-items:center;justify-content:center}
.slide-arrow{position:absolute}

/* products */
.products{top:2050px;height:690px;background:var(--white)}
.products h2{position:absolute;top:100px;width:100%;text-align:center;font-size:46px}
.card{position:absolute;width:216px;height:328px;border:2px solid var(--card-line);background:var(--white);text-align:center}
.card .pack{position:absolute;left:40px;top:22px;width:132px;height:170px;border-radius:40px 40px 20px 20px}
.card .name{position:absolute;top:212px;width:100%;font-weight:700;font-size:15px;text-transform:uppercase}
.card .price{position:absolute;top:240px;width:100%;font-size:15px;color:var(--red)}
.card .btn{left:59px;top:268px;width:96px;height:33px;font-size:12px}

/* guarantee */
.guarantee{top:2740px;height:411px;background:linear-gradient(180deg,#2d2e30 0%,#1e1f21 100%)}
.guarantee h2{position:absolute;top:80px;width:100%;text-align:center;font-size:46px;color:var(--white)}
.guarantee p{position:absolute;top:162px;left:150px;width:900px;text-align:center;font-size:16px;line-height:30px;color:var(--white)}

/* testimonial */
.testimonial{top:3151px;height:447px;background:var(--red-band);color:var(--white)}
.testimonial blockquote{position:absolute;top:172px;left:180px;width:840px;text-align:center;font-style:italic;font-size:26px;line-height:41px}
.testimonial cite{position:absolute;top:332px;width:100%;text-align:center;font-style:normal;font-weight:900;font-size:24px}

/* footer */
.footer{top:3598px;height:722px;background:linear-gradient(180deg,#2a2b2e 0%,#1c1d22 55%,#3a3324 85%,#1a1a1a 100%)}
.footer .brand{position:absolute;top:86px;width:100%;text-align:center;font-size:30px}
.social{position:absolute;top:158px;left:555px;display:flex;gap:8px}
.social-link{width:40px;height:40px;border-radius:50%;background:#050505;border:2px solid #3a3a3a;display:flex;align-items:center;justify-content:center}
.social-link i{display:block;width:12px;height:12px;border-radius:2px;background:var(--white)}
.footer-links{position:absolute;top:227px;width:100%;text-align:center;font-weight:700;font-size:14px;color:var(--white)}
.footer-links b{font-weight:400;margin:0 8px}
.copyright{position:absolute;top:278px;width:100%;text-align:center;font-size:14px;color:var(--white)}
.payments{position:absolute;top:327px;left:503px;display:flex;gap:8px}
.pay-badge{width:32px;height:22px;border-radius:3px;background:#f2f2f2;border:1px solid #bdbdbd;display:flex;align-items:center;justify-content:center}
.pay-badge i{display:block;width:20px;height:8px;border-radius:2px}
</style>
</head>
<body>

<section class="section hero">
  <div class="photo" role="img" aria-label="Red desert canyon with a rocky outcrop at dusk" style="inset:0"></div>
  <div class="brand">RIDGELYN</div>
  <nav class="nav">
    <span class="active" style="left:655px">MEALS</span>
    <span style="left:743px">QUARTER PADS</span>
    <span style="left:892px">SHOP NOW</span>
    <svg style="position:absolute;left:1016px;top:-8px" width="38" height="30" viewBox="0 0 38 30" fill="none" stroke="#e8202a" stroke-width="2.5"><path d="M2 3h6l4 16h18l4-12H10"/><circle cx="14" cy="25" r="2.5"/><circle cx="27" cy="25" r="2.5"/></svg>
  </nav>
  <h1 class="display">Quarter Pads To Keep<br>Your Meat Clean</h1>
  <p class="tagline">100% Waterproof<i>•</i>Lightweight<i>•</i>Quality Guarantee</p>
  <a class="btn" style="left:441px;top:488px;width:154px;height:49px">Shop Now <svg viewBox="0 0 14 14"><circle cx="7" cy="7" r="7" fill="#fff"/><path d="M6 4l3 3-3 3" stroke="#e8202a" stroke-width="2" fill="none"/></svg></a>
  <a class="btn btn-dark" style="left:605px;top:488px;width:156px;height:49px">Learn More <svg viewBox="0 0 14 14"><circle cx="7" cy="7" r="7" fill="#fff"/><path d="M6 4l3 3-3 3" stroke="#111" stroke-width="2" fill="none"/></svg></a>
  <svg class="play" width="56" height="56" viewBox="0 0 56 56"><circle cx="28" cy="28" r="25" fill="none" stroke="#fff" stroke-width="4"/><path d="M22 17l16 11-16 11z" fill="#fff"/></svg>
</section>

<section class="section problems">
  <div class="photo" role="img" aria-label="Quartered game meat resting on an orange pad beside a mountain lake" style="left:0;top:0;width:600px;height:617px;background:linear-gradient(180deg,#5d7285 0%,#44586a 35%,#3d4034 55%,#c8641f 75%,#a84e1a 100%)"></div>
  <h2 class="display">Do You <span class="accent">Still</span></h2>
  <ul class="checklist">
    <li><svg width="17" height="17" viewBox="0 0 17 17"><circle cx="8.5" cy="8.5" r="7" fill="none" stroke="#e8202a" stroke-width="2.2"/><path d="M5 8.7l2.5 2.5L12 6" stroke="#e8202a" stroke-width="2.2" fill="none"/></svg>Lay Your Fresh Meat On A Rock?</li>
    <li><svg width="17" height="17" viewBox="0 0 17 17"><circle cx="8.5" cy="8.5" r="7" fill="none" stroke="#e8202a" stroke-width="2.2"/><path d="M5 8.7l2.5 2.5L12 6" stroke="#e8202a" stroke-width="2.2" fill="none"/></svg>Sew Bed Sheets Together?</li>
    <li><svg width="17" height="17" viewBox="0 0 17 17"><circle cx="8.5" cy="8.5" r="7" fill="none" stroke="#e8202a" stroke-width="2.2"/><path d="M5 8.7l2.5 2.5L12 6" stroke="#e8202a" stroke-width="2.2" fill="none"/></svg>Use A Blue Tarp?</li>
    <li><svg width="17" height="17" viewBox="0 0 17 17"><circle cx="8.5" cy="8.5" r="7" fill="none" stroke="#e8202a" stroke-width="2.2"/><path d="M5 8.7l2.5 2.5L12 6" stroke="#e8202a" stroke-width="2.2" fill="none"/></svg>Lay Your Meat In The Dirt?</li>
    <li><svg width="17" height="17" viewBox="0 0 17 17"><circle cx="8.5" cy="8.5" r="7" fill="none" stroke="#e8202a" stroke-width="2.2"/><path d="M5 8.7l2.5 2.5L12 6" stroke="#e8202a" stroke-width="2.2" fill="none"/></svg>Stuff The Meat In Old Used Pillow Cases?</li>
  </ul>
  <p class="better">THERE IS A BETTER WAY</p>
  <a class="btn" style="left:672px;top:479px;width:322px;height:49px">Select My Quarter Pad <svg viewBox="0 0 14 14"><circle cx="7" cy="7" r="7" fill="#fff"/><path d="M6 4l3 3-3 3" stroke="#e8202a" stroke-width="2" fill="none"/></svg></a>
</section>

<section class="section benefits">
  <div class="photo" role="img" aria-label="Hunter in camouflage sitting beside a tent at camp" style="inset:0;background:radial-gradient(ellipse at 55% 40%,rgba(120,110,90,.35),transparent 60%)"></div>
  <h2 class="display">Be Responsible.Use <span class="accent">A Quarter Pad</span></h2>
  <svg class="slide-arrow" style="left:86px;top:290px" width="36" height="66" viewBox="0 0 36 66"><path d="M34 2L3 33l31 31" fill="none" stroke="#ddd" stroke-width="2"/></svg>
  <svg class="slide-arrow" style="left:1078px;top:290px" width="36" height="66" viewBox="0 0 36 66"><path d="M2 2l31 31L2 64" fill="none" stroke="#ddd" stroke-width="2"/></svg>
  <div class="feature" style="left:226px"><div class="ring"><svg width="70" height="60" viewBox="0 0 70 60" fill="none" stroke="#e8202a" stroke-width="3"><path d="M6 8h34M6 16h24"/><ellipse cx="42" cy="36" rx="20" ry="14"/><circle cx="44" cy="36" r="5"/><path d="M8 30h14M8 40h14"/></svg></div>Keep Your Meat<br>Off The Dirt</div>
  <div class="feature" style="left:416px"><div class="ring"><svg width="60" height="60" viewBox="0 0 60 60" fill="none" stroke="#e8202a" stroke-width="3"><path d="M12 50C20 26 34 12 52 8c-2 20-16 34-36 38z"/><path d="M8 54L40 22"/></svg></div>Lightweight</div>
  <div class="feature" style="left:605px"><div class="ring"><svg width="60" height="60" viewBox="0 0 60 60" fill="none" stroke="#e8202a" stroke-width="3"><path d="M46 22a18 18 0 1 1-30-6"/><path d="M12 8v10h10"/><rect x="22" y="18" width="16" height="24" rx="3"/></svg></div>Reusable</div>
  <div class="feature" style="left:794px"><div class="ring"><svg width="60" height="60" viewBox="0 0 60 60" fill="#e8202a"><path d="M36 6c8 12 12 18 12 24a12 12 0 0 1-24 0c0-6 4-12 12-24z"/><path d="M18 28c5 8 7 11 7 15a7 7 0 0 1-14 0c0-4 2-7 7-15z" fill="none" stroke="#e8202a" stroke-width="3"/></svg></div>100%<br>Waterproof</div>
  <div class="feature" style="left:985px"><div class="ring"><svg width="60" height="60" viewBox="0 0 60 60" fill="none" stroke="#e8202a" stroke-width="3"><path d="M18 14h24v40H18z"/><path d="M22 6h16v8H22z"/><path d="M30 30h12"/></svg></div>55”X60”<br>When Open</div>
  <a class="btn" style="left:439px;top:546px;width:322px;height:49px">Select My Quarter Pad <svg viewBox="0 0 14 14"><circle cx="7" cy="7" r="7" fill="#fff"/><path d="M6 4l3 3-3 3" stroke="#e8202a" stroke-width="2" fill="none"/></svg></a>
</section>

<section class="section products">
  <h2 class="display">Choose Your <span class="accent">Quarter Pad</span></h2>
  <div class="card" style="left:144px;top:238px">
    <div class="pack" role="img" aria-label="Red quarter pad in its stuff sack" style="background:linear-gradient(160deg,#d2262b,#9c1418)"></div>
    <p class="name">Red Quarter Pad</p><p class="price">$19.99</p><a class="btn">Buy Now</a>
  </div>
  <div class="card" style="left:375px;top:270px">
    <div class="pack" role="img" aria-label="Orange quarter pad in its stuff sack" style="background:linear-gradient(160deg,#ff8a3a,#e2621b)"></div>
    <p class="name">Orange Quarter Pad</p><p class="price">$19.99</p><a class="btn">Buy Now</a>
  </div>
  <div class="card" style="left:607px;top:238px">
    <div class="pack" role="img" aria-label="Orange XL quarter pad in its stuff sack" style="background:linear-gradient(160deg,#ff8a3a,#e2621b)"></div>
    <p class="name">XL Quarter Pad</p><p class="price">$29.99</p><a class="btn">Buy Now</a>
  </div>
  <div class="card" style="left:838px;top:270px">
    <div class="pack" role="img" aria-label="Green quarter pad in its stuff sack" style="background:linear-gradient(160deg,#2fc27a,#15955a)"></div>
    <p class="name">Green Quarter Pad</p><p class="price">$19.99</p><a class="btn">Buy Now</a>
  </div>
</section>

<section class="section guarantee">
  <div class="photo" role="img" aria-label="Game meat laid out on a pad at a dark campsite" style="inset:0;background:radial-gradient(ellipse at 50% 100%,rgba(120,70,40,.3),transparent 60%)"></div>
  <h2 class="display">100% Quality <span class="accent">Guarantee</span></h2>
  <p>We’ve designed our Quarter Pads for maximum performance and durability so you can keep the meat you harvest<br>in the backcountry clean and out of the dirt. If you are at all unsatisfied, contact us and we’ll make it right.</p>
  <a class="btn" style="left:439px;top:272px;width:322px;height:49px">Select My Quarter Pad <svg viewBox="0 0 14 14"><circle cx="7" cy="7" r="7" fill="#fff"/><path d="M6 4l3 3-3 3" stroke="#e8202a" stroke-width="2" fill="none"/></svg></a>
</section>

<section class="section testimonial">
  <svg style="position:absolute;left:552px;top:80px" width="96" height="64" viewBox="0 0 96 64" fill="none" stroke="#fff" stroke-width="3"><path d="M30 4a20 20 0 1 0 8 32c-2 12-12 22-24 26"/><path d="M80 4a20 20 0 1 0 8 32c-2 12-12 22-24 26"/></svg>
  <svg class="slide-arrow" style="left:66px;top:190px" width="36" height="66" viewBox="0 0 36 66"><path d="M34 2L3 33l31 31" fill="none" stroke="#fff" stroke-width="2"/></svg>
  <svg class="slide-arrow" style="left:1098px;top:190px" width="36" height="66" viewBox="0 0 36 66"><path d="M2 2l31 31L2 64" fill="none" stroke="#fff" stroke-width="2"/></svg>
  <blockquote>Gone are the days of struggling to keep a quarter from sliding off a log or rock while trying to de-bone meat. Packs small, weighs nothing, and keeps meat perfectly clean. It’s in my pack 100% of the time. Great Product!</blockquote>
  <cite>CODY HARLAN</cite>
</section>

<footer class="section footer">
  <div class="photo" role="img" aria-label="Glowing tents beneath a starry night sky in the mountains" style="inset:0;background:radial-gradient(ellipse at 40% 92%,rgba(230,190,60,.55),transparent 28%),radial-gradient(ellipse at 72% 92%,rgba(230,170,50,.4),transparent 22%)"></div>
  <div class="brand">RIDGELYN</div>
  <div class="social">
    <a class="social-link" aria-label="Social profile one"><i></i></a>
    <a class="social-link" aria-label="Social profile two"><i></i></a>
  </div>
  <p class="footer-links">MY ACCOUNT<b>/</b>BLOG<b>/</b>TERMS OF SERVICE AGREEMENT<b>/</b>REFUND AND RETURN POLICY<b>/</b>PRIVACY POLICY AGREEMENT</p>
  <p class="copyright">© 2020 Ridgelyn Outfitters.All Rights Reserved &nbsp;|&nbsp; Privacy &nbsp;|&nbsp; Terms and Use</p>
  <div class="payments" aria-label="Accepted payment methods">
    <span class="pay-badge"><i style="background:var(--badge-blue)"></i></span>
    <span class="pay-badge"><i style="background:var(--badge-orange)"></i></span>
    <span class="pay-badge"><i style="background:#8a8a8a"></i></span>
    <span class="pay-badge"><i style="background:var(--badge-sky)"></i></span>
    <span class="pay-badge"><i style="background:var(--badge-navy)"></i></span>
  </div>
</footer>

</body>
</html>
```